Business Card Design for company

We want new business cards. We'd like something different-- yet still highly professional. Our tagline is Providing leadership, delivering success. Stock photos are ok, as long as they are relevant and look upscale.

Target Market(s)

Architecture/Business Management Consulting/Engineering Consulting

Contact Information for Business Card

dark gray background with pops of blue might be good, but you tell me. You're the designers. Rounded corners might be nice, but again, you tell me.

Font styles to use
Serif
Sans Serif

Colors
3276b5
5c5c5c
9d9d9d
fbfbfb

Requirements
Nice to have
• Something different, but still very professional.

```html
<!DOCTYPE html>
<html lang="en">
<head>
<meta charset="utf-8">
<title>Travor Global — Business Card</title>
<link rel="stylesheet" href="https://fonts.googleapis.com/css2?family=Poppins:wght@400;500;600&display=swap">
<style>
  :root {
    --brand-blue: #3276b5;
    --brand-blue-light: #4a8ccb;
    --ink-dark: #5c5c5c;
    --ink-mid: #9d9d9d;
    --paper: #fbfbfb;
    --backdrop: #2e2a28;
    --white: #ffffff;
  }
  * { box-sizing: border-box; margin: 0; padding: 0; }
  html, body {
    width: 1200px; height: 1055px; overflow: hidden;
    background: var(--backdrop);
    font-family: "Poppins", sans-serif;
  }
  .stage { position: relative; width: 1200px; height: 1055px; }

  .card {
    position: absolute;
    width: 620px; height: 360px;
    border-radius: 26px;
    overflow: hidden;
    box-shadow: 0 14px 34px rgba(0,0,0,.45);
  }

  /* Front */
  .card-front {
    left: 60px; top: 110px;
    background: var(--brand-blue);
    color: var(--white);
  }
  .card-front .world-map {
    position: absolute; left: 40px; top: 30px; width: 540px; height: 290px;
    border-radius: 40px;
    background: radial-gradient(ellipse at 50% 45%, rgba(255,255,255,.12), rgba(255,255,255,0) 70%);
  }
  .card-front .wordmark {
    position: absolute; left: 0; right: 0; top: 118px;
    text-align: center;
    font-weight: 600; font-size: 58px; letter-spacing: 1px;
    color: var(--white);
  }
  .card-front .tagline {
    position: absolute; left: 34px; bottom: 38px;
    font-size: 17px; font-weight: 400; letter-spacing: .2px;
    display: flex; align-items: center; gap: 10px;
  }
  .tagline .bullet { width: 8px; height: 8px; background: var(--white); display: inline-block; }

  /* Back */
  .card-back {
    left: 520px; top: 585px;
    background: var(--paper);
    color: var(--ink-dark);
  }
  .card-back .wordmark {
    position: absolute; left: 36px; top: 146px; width: 330px;
    font-weight: 600; font-size: 40px; line-height: 1.1;
    color: var(--brand-blue);
  }
  .card-back .divider {
    position: absolute; left: 392px; top: 0; width: 2px; height: 100%;
    background: var(--brand-blue);
  }
  .contact-icons {
    position: absolute; left: 381px; top: 0;
  }
  .contact-details {
    position: absolute; left: 420px; top: 96px; width: 200px;
    font-size: 13.5px; line-height: 1.35;
  }
  .contact-details .name {
    font-weight: 600; font-size: 17px; color: var(--brand-blue); letter-spacing: .3px;
  }
  .contact-details .role { margin-bottom: 14px; }
  .contact-details .address { margin-bottom: 12px; }
  .contact-details .web .accent { color: var(--brand-blue); }
</style>
</head>
<body>
<main class="stage">

  <section class="card card-front" aria-label="Card front">
    <div class="world-map" role="img" aria-label="Faint world map behind the company name"></div>
    <div class="wordmark">TRAVOR GLOBAL</div>
    <p class="tagline">
      <span class="bullet"></span>Providing leadership
      <span class="bullet"></span>Delivering success
    </p>
  </section>

  <section class="card card-back" aria-label="Card back">
    <div class="wordmark">TRAVOR<br>GLOBAL</div>
    <div class="divider"></div>

    <svg class="contact-icons" width="24" height="360" viewBox="0 0 24 360" aria-hidden="true">
      <g fill="var(--brand-blue)">
        <circle cx="12" cy="104" r="10"/>
        <circle cx="12" cy="153" r="10"/>
        <circle cx="12" cy="209" r="10"/>
        <circle cx="12" cy="229" r="10"/>
        <circle cx="12" cy="249" r="10"/>
        <circle cx="12" cy="269" r="10"/>
      </g>
      <g fill="var(--white)" stroke="var(--white)">
        <!-- person -->
        <circle cx="12" cy="101" r="2.6" stroke="none"/>
        <path d="M7 110 q5 -7 10 0 z" stroke="none"/>
        <!-- pin -->
        <path d="M12 159 l-4 -6 a4 4 0 1 1 8 0 z" stroke="none"/>
        <circle cx="12" cy="152" r="1.4" fill="var(--brand-blue)" stroke="none"/>
        <!-- phone -->
        <path d="M8 205 q0 9 8 9 l1 -2 -2.5 -2 -1.5 1 q-3 -1 -3.5 -3.5 l1 -1.5 -2 -2.5 z" stroke="none"/>
        <!-- fax / printer -->
        <rect x="9" y="224" width="6" height="4" stroke="none"/>
        <rect x="7" y="228" width="10" height="5" rx="1" stroke="none"/>
        <!-- mail -->
        <rect x="7" y="265.5" width="10" height="7" fill="none" stroke-width="1.4" transform="translate(0 -20)"/>
        <path d="M7 246 l5 4 5 -4" fill="none" stroke-width="1.4"/>
        <!-- globe -->
        <circle cx="12" cy="269" r="5.5" fill="none" stroke-width="1.3"/>
        <path d="M6.5 269 h11 M12 263.5 v11" fill="none" stroke-width="1"/>
        <ellipse cx="12" cy="269" rx="2.5" ry="5.5" fill="none" stroke-width="1"/>
      </g>
    </svg>

    <div class="contact-details">
      <p class="name">DANIEL HARTLEY</p>
      <p class="role">Resident Manager</p>
      <p class="address">418 W Harbor Ave. Ste 210B<br>Bayview, VA 23610</p>
      <p>+1 555.204.7731</p>
      <p>+1 555.318.4092</p>
      <p>info@travorglobal.com</p>
      <p class="web">www.<span class="accent">travorglobal</span>.com</p>
    </div>
  </section>

</main>
</body>
</html>
```